Clean business card with logo provided

I want a card that will stand out among the masses. I need the color and image to show professionalism and yet have a family appeal showing that I only deal with win/win scenarios. The back of the card will be used to take notes about the individual so I can use that in my database entry. I like modern design but need professionalism in it also. It needs to fit my "clean, safe, and affordable housing" motto. I need to be able to write on the file and update the card details for my employees.

Target Market(s)

Investors looking to make investment income through real estate

Industry/Entity Type

Real Estate

Contact Information for Business Card

Brent Kovalich
blank address, city, st, zip code
480-555-3174
brentkovalich@ridgeworthrentals.example
www.ridgeworthrentals.example

Font styles to use
Sans Serif

Requirements
Must have
• I would like the back of the card to have lines for info. example
• Met/Visited: Date:
• Interets:
Nice to have
• I want the cards color to match the logo background color. Font with details to be san serif and black. I want the card rectangular with square corners. Standard business card size. I would like to see cards designed with both images to see which i prefer more.

```html
<!DOCTYPE html>
<html lang="en">
<head>
<meta charset="utf-8">
<title>Ridgeworth Rentals LLC – Business Card</title>
<link rel="stylesheet" href="https://fonts.googleapis.com/css2?family=Montserrat:wght@400;500&family=Open+Sans:wght@400;600&display=swap">
<style>
  :root {
    --teal: #00b8cc;
    --ink: #050505;
    --paper: #f4f4f4;
    --white: #ffffff;
    --stage: #e6e3de;
  }
  * { box-sizing: border-box; margin: 0; padding: 0; }
  html, body { width: 1200px; height: 864px; overflow: hidden; }
  body {
    background: var(--stage);
    display: flex;
    flex-direction: column;
    align-items: center;
    justify-content: center;
    gap: 40px;
    font-family: "Open Sans", Arial, sans-serif;
  }
  .card {
    position: relative;
    width: 660px;
    height: 377px;
    overflow: hidden;
  }

  /* Wordmark */
  .wordmark {
    position: absolute;
    font-family: "Montserrat", Arial, sans-serif;
    font-weight: 400;
    line-height: 1;
  }
  .wordmark .name { display: block; font-size: 54px; letter-spacing: 2px; }
  .wordmark .suffix { display: block; font-size: 18px; letter-spacing: 11px; margin-top: 6px; padding-left: 4px; }
  .tagline {
    position: absolute;
    font-family: "Open Sans", Arial, sans-serif;
    font-size: 15px;
    font-weight: 600;
    letter-spacing: 0.5px;
  }

  /* Front */
  .card-front { background: var(--ink); color: var(--white); }
  .card-front .wordmark { left: 40px; top: 34px; color: var(--teal); }
  .card-front .tagline { left: 42px; top: 128px; color: var(--teal); }
  .front-rule {
    position: absolute;
    left: 0; top: 186px;
    width: 322px; height: 2px;
    background: var(--white);
  }
  .holder {
    position: absolute;
    right: 40px; top: 166px;
    height: 42px;
    display: flex;
    align-items: center;
    gap: 14px;
    font-family: "Montserrat", Arial, sans-serif;
    font-weight: 500;
    font-size: 32px;
    line-height: 1;
    color: var(--teal);
    white-space: nowrap;
  }
  .holder .dot { width: 22px; height: 22px; border-radius: 50%; background: var(--white); flex: none; }
  .contact-list {
    position: absolute;
    left: 40px; top: 222px;
    list-style: none;
  }
  .contact-list li {
    display: flex;
    align-items: center;
    gap: 14px;
    font-size: 17px;
    line-height: 30px;
    color: var(--white);
    white-space: nowrap;
  }
  .contact-list .icon { width: 14px; height: 14px; flex: none; }

  /* Back */
  .card-back { background: var(--paper); color: var(--ink); }
  .back-band {
    position: absolute;
    left: 0; top: 0;
    width: 100%; height: 178px;
    background: var(--teal);
    border-bottom: 5px solid var(--ink);
  }
  .card-back .wordmark { left: 150px; top: 36px; color: var(--ink); }
  .card-back .tagline { left: 152px; top: 132px; color: var(--white); }
  .notes {
    position: absolute;
    left: 40px; top: 210px; right: 40px;
    list-style: none;
  }
  .notes li {
    display: flex;
    align-items: flex-end;
    gap: 12px;
    height: 38px;
    font-size: 22px;
    font-family: "Open Sans", Arial, sans-serif;
  }
  .notes .label { white-space: nowrap; }
  .notes .write-line { flex: 1; border-bottom: 2px solid var(--ink); margin-bottom: 6px; }
</style>
</head>
<body>

  <section class="card card-front" aria-label="Business card front">
    <div class="wordmark">
      <span class="name">RIDGEWORTH</span>
      <span class="suffix">RENTALS LLC</span>
    </div>
    <p class="tagline">Providing clean, safe, and affordable housing</p>
    <div class="front-rule"></div>

    <div class="holder">
      <span class="holder-name">Brent Kovalich</span>
      <span class="dot"></span>
    </div>

    <ul class="contact-list">
      <li>
        <svg class="icon" viewBox="0 0 14 14" aria-hidden="true">
          <rect width="14" height="14" fill="var(--teal)"/>
          <path d="M4 3h2l1 2-1.2 1a5 5 0 0 0 2.2 2.2L9 7l2 1v2a1 1 0 0 1-1 1A7 7 0 0 1 3 4a1 1 0 0 1 1-1z" fill="var(--ink)"/>
        </svg>
        480-555-3174
      </li>
      <li>
        <svg class="icon" viewBox="0 0 14 14" aria-hidden="true">
          <rect width="14" height="14" fill="var(--teal)"/>
          <circle cx="7" cy="7" r="4" fill="none" stroke="var(--ink)" stroke-width="1.2"/>
          <path d="M3 7h8M7 3c-2 2.5-2 5.5 0 8M7 3c2 2.5 2 5.5 0 8" fill="none" stroke="var(--ink)" stroke-width="1"/>
        </svg>
        www.ridgeworthrentals.example
      </li>
      <li>
        <svg class="icon" viewBox="0 0 14 14" aria-hidden="true">
          <rect width="14" height="14" fill="var(--teal)"/>
          <rect x="3" y="4" width="8" height="6" fill="none" stroke="var(--ink)" stroke-width="1.2"/>
          <path d="M3 4l4 3.2L11 4" fill="none" stroke="var(--ink)" stroke-width="1.2"/>
        </svg>
        brentkovalich@ridgeworthrentals.example
      </li>
      <li>
        <svg class="icon" viewBox="0 0 14 14" aria-hidden="true">
          <rect width="14" height="14" fill="var(--teal)"/>
          <path d="M7 12s-3.5-3.8-3.5-6.2a3.5 3.5 0 0 1 7 0C10.5 8.2 7 12 7 12z" fill="var(--ink)"/>
          <circle cx="7" cy="5.8" r="1.2" fill="var(--teal)"/>
        </svg>
        2750 Alder Ave, Marlow Springs, IL 60999
      </li>
    </ul>
  </section>

  <section class="card card-back" aria-label="Business card back">
    <div class="back-band"></div>
    <div class="wordmark">
      <span class="name">RIDGEWORTH</span>
      <span class="suffix">RENTALS LLC</span>
    </div>
    <p class="tagline">Providing clean, safe, and affordable housing</p>

    <ul class="notes">
      <li><span class="label">Met/Visited: Date:</span><span class="write-line"></span></li>
      <li><span class="label">Interets:</span><span class="write-line"></span></li>
      <li><span class="label">Problems:</span><span class="write-line"></span></li>
    </ul>
  </section>

</body>
</html>
```